Call Center In Need of Website Design

We are a call center that provides inbound and outbound calling & marketing services for eCommerce store. We would like to see a fun, creative, playful design that is simple.

Here are some sample design sites we like;
- https://www.velmoreline.com/
- https://pindrask.io/
- https://www.glimbertic.com/live-chat-software/
- https://www.zavrolin.com/

Here are some competitor sites;
- https://www.ostrevaglinks.com/
- https://www.helpkestrel.com/

I have attached website content for your use.

Target Market(s)

eCommerce

Coding

Coded - Design and coding required

Number of Pages Required

5+ page

Font styles to use
Sans Serif

Colors

Designer to choose colors to be used in the design.

Requirements
Must have
• Must have designs for the following 5 separate pages;
• 1. Home (landing)
• - This will be were the design style really needs to show.
• - Just needs to touch on key services
• - CTA
• 2. About Us
• - Basic page for about me paragraph
• 3. Services
• - List of services with icons
• - Click on service type to expand details or hover over service icon to view popup bubble with details about that service
• 4. Pricing
• - Option to bundle 1(one) digital service plan and 1(one) call center service plan
• - Bundling adds 10% monthly discount to over all price
• - Customer does NOT have to bundle
• - FAQ
• 5. Contact Us
• - Include a capture form (name, company name, email, phone, message)
• - Contact info
• - Business hours
• When customer purchases their desired plan, then they are taken to a page where they must schedule a call with an account rep.
Nice to have
• home page animations
Should not have
• All information on Home/Landing page.

```html
<!DOCTYPE html>
<html lang="en">
<head>
<meta charset="utf-8">
<title>Corvala — Customer Service</title>
<link rel="stylesheet" href="https://fonts.googleapis.com/css2?family=Poppins:wght@400;500;600;700&display=swap">
<style>
:root{
  --teal:#5fc4a8;
  --teal-dark:#4fb497;
  --ink:#333333;
  --muted:#555555;
  --light:#ebebeb;
  --card:#eeeeee;
  --white:#ffffff;
  --footer:#0e0e0e;
  --bar:#000000;
  --pill-dark:#555555;
}
*{margin:0;padding:0;box-sizing:border-box}
html,body{width:1200px;height:2731px;overflow:hidden}
body{font-family:'Poppins',sans-serif;color:var(--ink);background:var(--white);position:relative}
.abs{position:absolute}

/* header */
.site-header{position:absolute;left:0;top:0;width:1200px;height:95px;background:var(--white)}
.brand{position:absolute;display:flex;align-items:center;gap:16px;font-weight:500;letter-spacing:6px}
.brand .dot{width:44px;height:44px;border:3px solid var(--teal);border-radius:50%}
.site-header .brand{left:104px;top:24px;font-size:30px;color:#444}
.main-nav{position:absolute;top:36px;left:0;font-size:16px;color:#333}
.main-nav a{position:absolute;white-space:nowrap;color:inherit;text-decoration:none}
.main-nav a.active{color:var(--teal)}
.search-icon{position:absolute;left:1082px;top:36px}

/* hero */
.hero{position:absolute;left:0;top:95px;width:1200px;height:599px;
  background:linear-gradient(90deg,#3c4a58 0%,#5a6a78 45%,#7b8894 70%,#4a5866 100%)}
.hero-title{position:absolute;left:98px;top:175px;font-size:40px;line-height:49px;font-weight:600;color:var(--white)}
.hero-text{position:absolute;left:104px;top:285px;width:520px;font-size:15px;line-height:27px;font-weight:500;color:var(--white)}
.btn{position:absolute;display:flex;align-items:center;justify-content:center;border-radius:30px;font-weight:600;text-transform:uppercase;font-size:14px;color:var(--white);background:var(--teal)}
.hero .btn{left:98px;top:360px;width:166px;height:54px;font-size:15px}
.slider-dots{position:absolute;left:570px;top:529px;display:flex;gap:10px;align-items:center}
.slider-dots span{width:10px;height:10px;border-radius:50%;background:var(--white)}
.slider-dots span.on{width:20px;height:20px;border:2px solid var(--white);background:transparent;position:relative}
.slider-dots span.on::after{content:"";position:absolute;left:3px;top:3px;width:10px;height:10px;border-radius:50%;background:var(--white)}

/* about */
.about{position:absolute;left:0;top:694px;width:1200px;height:417px;background:var(--light);overflow:hidden}
.section-title{font-weight:600;color:var(--teal)}
.about .section-title{position:absolute;left:104px;top:88px;font-size:30px}
.about p{position:absolute;left:104px;top:142px;width:450px;font-size:14.5px;line-height:27.5px;color:#444}
.about .btn{left:104px;top:297px;width:127px;height:34px;font-size:13px}
.about-frame{position:absolute;left:643px;top:29px;width:262px;height:362px;border:4px solid var(--teal)}
.about-photo{position:absolute;left:672px;top:54px;width:342px;height:310px;background:linear-gradient(135deg,#c9b6a6,#e8ddd3 50%,#a98d78)}

/* what we do */
.what{position:absolute;left:0;top:1111px;width:1200px;height:448px;
  background:linear-gradient(90deg,#6a6a6a 0%,#7c7c7c 40%,#9a9a9a 60%,#5a5f66 100%)}
.what h2{position:absolute;left:99px;top:90px;font-size:30px;font-weight:600;color:var(--white)}
.what p{position:absolute;left:99px;top:146px;width:560px;font-size:14.5px;line-height:27.5px;font-weight:500;color:var(--white)}
.btn-outline{position:absolute;left:99px;top:315px;width:130px;height:35px;border:2px solid var(--white);border-radius:30px;color:var(--white);font-size:13px;font-weight:600;display:flex;align-items:center;justify-content:center}

/* services */
.services{position:absolute;left:0;top:1559px;width:1200px;height:837px;background:var(--white)}
.services .section-title{position:absolute;left:0;width:1200px;text-align:center;top:68px;font-size:32px}
.tab{position:absolute;top:153px;height:49px;border-radius:30px;display:flex;align-items:center;justify-content:center;font-size:17px;font-weight:600;color:var(--white)}
.tab.digital{left:388px;width:187px;background:var(--teal)}
.tab.call{left:594px;width:218px;background:var(--pill-dark)}
.service-card{position:absolute;width:311px;height:225px;background:var(--card);box-shadow:0 3px 8px rgba(0,0,0,.18);text-align:center}
.service-card svg{position:absolute;left:50%;top:30px;transform:translateX(-50%)}
.service-card h3{position:absolute;left:0;right:0;top:98px;font-size:16.5px;font-weight:500;color:var(--teal)}
.service-card p{position:absolute;left:20px;right:20px;top:124px;font-size:15px;line-height:24px;color:#444}
.service-card .more{position:absolute;left:0;right:0;top:182px;font-size:16.5px;font-weight:500;color:var(--teal)}

/* footer */
.site-footer{position:absolute;left:0;top:2396px;width:1200px;height:272px;background:var(--footer);color:var(--white)}
.site-footer .brand{left:100px;top:50px;font-size:26px;color:var(--white)}
.site-footer .brand .dot{width:40px;height:40px}
.footer-about{position:absolute;left:102px;top:114px;width:250px;font-size:13.5px;line-height:22px}
.social{position:absolute;left:102px;top:206px;display:flex;gap:12px}
.social span{width:13px;height:13px;border-radius:50%;background:var(--white)}
.footer-head{position:absolute;top:44px;font-size:16px;font-weight:600;letter-spacing:.3px}
.footer-links{position:absolute;left:405px;top:88px;list-style:none;font-size:14px;line-height:26px}
.contact-row{position:absolute;left:575px;display:flex;gap:15px;font-size:13px;line-height:24px}
.contact-row svg{flex:none;margin-top:4px}
.newsletter-text{position:absolute;left:852px;top:92px;width:250px;font-size:13.5px;line-height:26px}
.newsletter-form{position:absolute;left:852px;top:190px;width:239px;height:39px;display:flex}
.newsletter-form .field{flex:1;background:var(--white);color:#888;font-size:11px;font-style:italic;display:flex;align-items:center;padding-left:12px}
.newsletter-form .go{width:44px;background:var(--teal);display:flex;align-items:center;justify-content:center}
.copyright{position:absolute;left:0;top:2668px;width:1200px;height:63px;background:var(--bar);color:var(--white);font-size:13px;display:flex;align-items:center;justify-content:center}
</style>
</head>
<body>

<header class="site-header">
  <div class="brand"><span class="dot"></span>CORVALA</div>
  <nav class="main-nav">
    <a class="active" style="left:572px">Home</a>
    <a style="left:659px">About Us</a>
    <a style="left:767px">Services</a>
    <a style="left:872px">Pricing</a>
    <a style="left:965px">Contact Us</a>
  </nav>
  <svg class="search-icon" width="18" height="18" viewBox="0 0 18 18" fill="none" stroke="#5fc4a8" stroke-width="2.2"><circle cx="7.5" cy="7.5" r="5.5"/><path d="M11.5 11.5l5 5"/></svg>
</header>

<section class="hero" role="img" aria-label="Photo of customer service agents wearing headsets in a bright office">
  <h1 class="hero-title">We Offer instant and quality<br>Customer Service!</h1>
  <p class="hero-text">At vero eos et accusamus et iusto odio dignissimos ducimus qui blanditiis praesentium voluptatum deleniti atque.</p>
  <span class="btn">Read More</span>
  <div class="slider-dots"><span class="on"></span><span></span><span></span></div>
</section>

<section class="about">
  <svg class="abs" style="left:0;top:0" width="1200" height="417"><polygon points="910,0 1200,0 1200,417 828,417" fill="#5fc4a8"/></svg>
  <h2 class="section-title">About Us</h2>
  <p>Corvala is an omnichannel provider for customer care and back-end office support. We primarily work with eCommerce companies around the world. Our service is vital to the core operations and functionality of consumer-focused online eCommerce companies</p>
  <span class="btn">Read More</span>
  <div class="about-frame"></div>
  <div class="about-photo" role="img" aria-label="Photo of a smiling support agent wearing a headset"></div>
</section>

<section class="what" role="img" aria-label="Photo of a support agent with glasses on a call at his desk">
  <h2>What We Do</h2>
  <p>Corvala is your personal customer service and product research team. We love eCommerce, but we love seeing business owners succeed even more! That is exactly why we have developed the processes and technology to take care of the most over looked areas in eCommerce - Customer Service and Retention.</p>
  <span class="btn-outline">READ MORE</span>
</section>

<section class="services">
  <h2 class="section-title">Services</h2>
  <span class="tab digital">Digital Services</span>
  <span class="tab call">Call Center Services</span>

  <article class="service-card" style="left:98px;top:256px">
    <svg width="56" height="40" viewBox="0 0 56 40" fill="#5fc4a8"><rect x="1" y="2" width="54" height="36" rx="2"/><path d="M3 4l25 20 25-20" fill="none" stroke="#eee" stroke-width="2.5"/><path d="M3 36l18-16M53 36L35 20" stroke="#eee" stroke-width="2.5"/></svg>
    <h3>Email Support</h3>
    <p>At vero eos et accusamus et iusto odio dignissimos ducimus</p>
    <span class="more">Read More</span>
  </article>
  <article class="service-card" style="left:444px;top:256px">
    <svg width="56" height="54" viewBox="0 0 56 54" fill="none" stroke="#5fc4a8" stroke-width="2"><path d="M6 6h36v32H18l-10 8v-8H6z"/><path d="M14 12h36v32h-4v8l-10-8H22"/><circle cx="32" cy="28" r="7"/><circle cx="32" cy="28" r="2.5"/></svg>
    <h3>Live Chat Support</h3>
    <p>At vero eos et accusamus et iusto odio dignissimos ducimus</p>
    <span class="more">Read More</span>
  </article>
  <article class="service-card" style="left:790px;top:256px">
    <svg width="56" height="54" viewBox="0 0 56 54" fill="none" stroke="#5fc4a8" stroke-width="2"><rect x="4" y="4" width="36" height="30"/><path d="M10 26l8-8 6 5 10-10"/><circle cx="38" cy="34" r="9"/><path d="M44 41l8 9"/></svg>
    <h3>Product Research</h3>
    <p>At vero eos et accusamus et iusto odio dignissimos ducimus</p>
    <span class="more">Read More</span>
  </article>

  <article class="service-card" style="left:98px;top:513px">
    <svg width="56" height="56" viewBox="0 0 56 56" fill="none" stroke="#5fc4a8" stroke-width="2"><rect x="4" y="4" width="48" height="48"/><path d="M4 13h48"/><path d="M11 22l3 3 5-5M11 33l3 3 5-5M11 44l3 3 5-5M24 24h20M24 35h20M24 46h20"/></svg>
    <h3>Product Listing</h3>
    <p>At vero eos et accusamus et iusto odio dignissimos ducimus</p>
    <span class="more">Read More</span>
  </article>
  <article class="service-card" style="left:444px;top:513px">
    <svg width="58" height="56" viewBox="0 0 58 56" fill="none" stroke="#5fc4a8" stroke-width="2"><rect x="3" y="4" width="52" height="38"/><path d="M12 36V26M20 36V20M28 36V24M36 36V14M44 36V18"/><path d="M29 42v8M18 52h22"/></svg>
    <h3>Price Monitoring</h3>
    <p>At vero eos et accusamus et iusto odio dignissimos ducimus</p>
    <span class="more">Read More</span>
  </article>
  <article class="service-card" style="left:790px;top:513px">
    <svg width="64" height="52" viewBox="0 0 64 52" fill="none" stroke="#5fc4a8" stroke-width="2"><rect x="3" y="6" width="46" height="36"/><circle cx="26" cy="24" r="10"/><path d="M23 19v10l8-5z"/><path d="M42 44l16-22 4 3-16 22-5 1z"/></svg>
    <h3>Product Photo &amp; Video Editing</h3>
    <p>At vero eos et accusamus et iusto odio dignissimos ducimus</p>
    <span class="more">Read More</span>
  </article>
</section>

<footer class="site-footer">
  <div class="brand"><span class="dot"></span>CORVALA</div>
  <p class="footer-about">At vero eos et accusamus et iusto odio dignissimos ducimus qui blanditiis</p>
  <div class="social" aria-label="Social links"><span></span><span></span><span></span><span></span></div>

  <h4 class="footer-head" style="left:405px">LINKS</h4>
  <ul class="footer-links"><li>Home</li><li>About Us</li><li>Services</li><li>Pricing</li><li>Contact Us</li></ul>

  <h4 class="footer-head" style="left:576px">CONTACT US</h4>
  <div class="contact-row" style="top:86px">
    <svg width="14" height="18" viewBox="0 0 14 18" fill="#fff"><path d="M7 0a7 7 0 0 0-7 7c0 5 7 11 7 11s7-6 7-11a7 7 0 0 0-7-7zm0 10a3 3 0 1 1 0-6 3 3 0 0 1 0 6z"/></svg>
    <span>Corvala, Inc. 418 Larkmoor Ave.<br>Denton, CA 90814</span>
  </div>
  <div class="contact-row" style="top:152px">
    <svg width="16" height="16" viewBox="0 0 16 16" fill="#fff"><path d="M3.5 0l3 4-2 2c1 2 3 4 5 5l2-2 4 3-2 3C7 15 1 9 0 3z"/></svg>
    <span>(800) 555-0148</span>
  </div>
  <div class="contact-row" style="top:194px">
    <svg width="17" height="12" viewBox="0 0 17 12" fill="#fff"><rect width="17" height="12" rx="1"/><path d="M1 1l7.5 6L16 1" fill="none" stroke="#0e0e0e" stroke-width="1.4"/></svg>
    <span>info@corvala.com</span>
  </div>

  <h4 class="footer-head" style="left:852px">NEWSLETTER</h4>
  <p class="newsletter-text">But I must explain to you how all this mistaken idea of denouncing pleasure and praising.</p>
  <div class="newsletter-form">
    <span class="field">Enter your email address</span>
    <span class="go"><svg width="14" height="12" viewBox="0 0 14 12" fill="none" stroke="#fff" stroke-width="2"><path d="M0 6h12M7 1l5 5-5 5"/></svg></span>
  </div>
</footer>
<div class="copyright">© 2018 Corvala, Inc | All Rights Reserved</div>

</body>
</html>
```